Slow Winter Song. A CD of beautiful 17th century music for lute played by a world famous lutenist.

Hi designers,
My name is Ollie Pellicott and I am an international lute player in need of a CD cover design. I am blind, so will be relying on other people's eyes and descriptions during the process, including yours! Are you up for the challenge?
My CD is called Slow Winter Song. It's beautiful lute music from the 17th century, very intimate and carming, but also very powerful.
I would like you to use the attached image, and find a way to include the following text in a tasteful way:
The text for the front cover is as follows:
Slow Winter Song
Oliver Pellicott - lute and theorbo
Music by Harcrane, Fennimore, Brackley, Tarn, Cavallenti and Ruhlendorf.
Here is a viewora link to some of the music I play, which should give you an idea:
www.viewora.net/olliepellicott1
Here is a link to my website, where you can see the covers of my other CDs, and get more information about me:
www.oliverpellicott.net
I'm excited to receive your design and ideas.
Best wishes
Ollie

```html
<!DOCTYPE html>
<html lang="en">
<head>
<meta charset="utf-8">
<title>Slow Winter Song — Oliver Pellicott</title>
<link href="https://fonts.googleapis.com/css2?family=Cinzel:wght@400;500&family=Michroma&family=Mrs+Saint+Delafield&display=swap" rel="stylesheet">
<style>
  :root {
    --paper: #efece3;
    --cartouche: #f1eee6;
    --frame: #6e6e6e;
    --title-red: #8e1a1f;
    --ink: #1c1c1c;
    --scene-light: #d9d6cf;
    --scene-mid: #a7a49c;
    --scene-dark: #5e5c57;
    --pill: rgba(240, 237, 229, 0.88);
  }
  * { box-sizing: border-box; margin: 0; padding: 0; }
  html, body { width: 1200px; height: 1200px; overflow: hidden; background: #ffffff; }

  .cover {
    position: relative;
    width: 1200px;
    height: 1200px;
    overflow: hidden;
    background: var(--paper);
  }

  .cover__backdrop {
    position: absolute;
    inset: 0;
    background:
      radial-gradient(ellipse at 50% 35%, rgba(235,232,225,0.0) 30%, rgba(60,58,54,0.35) 100%),
      linear-gradient(180deg, var(--scene-light) 0%, #c4c1b9 35%, var(--scene-mid) 65%, var(--scene-dark) 100%);
  }

  .cover__instrument {
    position: absolute;
    left: 0;
    top: 330px;
    width: 560px;
    height: 845px;
    border-radius: 0 60px 280px 0;
    background: linear-gradient(160deg, rgba(250,248,242,0.75) 0%, rgba(232,229,220,0.9) 60%, rgba(205,201,192,0.9) 100%);
  }

  .cartouche {
    position: absolute;
    left: 346px;
    top: 75px;
    width: 564px;
    height: 822px;
  }
  .cartouche svg { position: absolute; inset: 0; }

  .title {
    position: absolute;
    left: 0;
    right: 0;
    top: 135px;
    text-align: center;
    font-family: "Cinzel", serif;
    font-weight: 400;
    color: var(--title-red);
    font-size: 108px;
    line-height: 140px;
    letter-spacing: 1px;
  }
  .title span { display: block; }

  .subtitle {
    position: absolute;
    left: 0;
    right: 0;
    top: 560px;
    text-align: center;
    font-family: "Mrs Saint Delafield", cursive;
    font-size: 48px;
    line-height: 56px;
    color: var(--ink);
  }
  .subtitle span { display: block; }
  .subtitle span:first-child { padding-left: 10px; }
  .subtitle span:last-child { padding-left: 40px; }

  .credit {
    position: absolute;
    left: 50%;
    transform: translateX(-50%);
    background: var(--pill);
    border-radius: 44px;
    text-align: center;
    font-family: "Michroma", sans-serif;
    color: var(--ink);
  }
  .credit--artist {
    top: 855px;
    width: 660px;
    padding: 18px 0 16px;
    font-size: 23px;
    line-height: 36px;
    letter-spacing: 2px;
  }
  .credit--composers {
    top: 990px;
    width: 700px;
    padding: 12px 0 14px;
    font-size: 18px;
    line-height: 28px;
    letter-spacing: 0.5px;
  }
  .credit--composers .credit__label { font-size: 17px; }
</style>
</head>
<body>
  <main class="cover">
    <div class="cover__backdrop" role="img" aria-label="Sepia photograph of a stone castle with towers behind trees"></div>
    <div class="cover__instrument" role="img" aria-label="Engraved illustration of a lute lying diagonally"></div>

    <div class="cartouche">
      <svg viewBox="0 0 564 822" width="564" height="822" aria-hidden="true">
        <path d="M40 60 H200 Q282 0 364 60 H524 V80 H544 V250 Q580 420 544 590 V760 H524 V782 H364 Q282 830 200 782 H40 V760 H20 V590 Q-16 420 20 250 V80 H40 Z"
              fill="var(--cartouche)" stroke="var(--frame)" stroke-width="5"/>
        <path d="M50 72 H204 Q282 18 360 72 H514 V90 H532 V252 Q566 420 532 588 V750 H514 V770 H360 Q282 814 204 770 H50 V750 H32 V588 Q-2 420 32 252 V90 H50 Z"
              fill="none" stroke="var(--frame)" stroke-width="2"/>
      </svg>
      <h1 class="title"><span>Slow</span><span>Winter</span><span>Song</span></h1>
      <p class="subtitle"><span>17th century</span><span>music for lute</span></p>
    </div>

    <div class="credit credit--artist">
      <p>OLIVER PELLICOTT</p>
      <p>LUTE AND THEORBO</p>
    </div>
    <div class="credit credit--composers">
      <p class="credit__label">MUSIC BY:</p>
      <p>HARCRANE • FENNIMORE • BRACKLEY</p>
      <p>TARN • CAVALLENTI • RUHLENDORF</p>
    </div>
  </main>
</body>
</html>
```